Dietary supplement, Clean and simple.

Hi,
I’d like to talk about the project,

About us:
We are a dietary supplement (Vitamins, Minerals, amino acids etc.) company.
The goal is to have about 25 products at the end of this year. However, for this goal to be achieved we need a good label design to make our products represent our company values.
I’ll be here every day supporting your questions, we are fully committed to making the highest/best quality/customer experience possible.

About the design and our values:
- Professional (We are in the industry of professionalism and expertise. I would love to show we are competent at this, Id. Like to have the labels looks like we have done our research.)
- Efficient (White spacing, good use of the space available.)
- Simple (Straight forward, in 5 seconds they have to know what the product they have is/how functions. We’re trying to simplify it for the consumer.
- No distractions (the only visually “distracting” factor can be the vector art.)

The guidelines:
The goal is to have a universal design, with one element that changes (Vector art). I’ll attach a file/multiple files I think can show some visuals on what I’m looking for, and what parts of the design I think are good/bad.

Label size: 69x155mm (Front is 77.5mm)

Design whatever you think fits our image. You’re the design expert, all I care about is that it fits our company standards/image.

Use this color/font.
Font: Sans Serif
Main company color is Mind green #237D62 (Use this color for something in the design.)

What I thought would be cool/might looks ugly, who knows:
1. The front of the label: Should have 1 vector art, preferably in the top right corner. (That looks good in multiple colors. The vector can have multiple areas to color, I would prefer 2 main colors in the vector art. The interchangeable colors are used for multiple kinds of products.)
2. Text/product information on the left. The text that will have to be displayed:
- Product name for instance “Magnesium + B6”
- Description for the product for instance “Magnesium with ginger taste”
- Company name or logo. (Add ® behind it. We are soon to be trademark registered.)
3. We need to show the "daily intake" amount on the front and also the amount in the complete bottle. For instance, “Daily intake 1 capsule, 60 capsules”.
• You don’t have to design the backside of the label. After I chose a design, I’d like to chat and give specific information on what areas need to be assigned where. (Too complex because of the law.)
Updates

Hi, Please make the deadline 31 days total. I want designers to have the time to design. And not be rushed to finish it.

I want to extend the deadline because i feel like a slightly more medical look would be interesting. Hope you can come up with something!!

Target Market(s)

Dietary supplement consumers

Industry/Entity Type

Dietary supplements

Font styles to use
Sans Serif

Colors

Designer to choose colors to be used in the design.

Requirements
Must have
• Trademark icon "®" has to be at the top right after the company logo(text of logo)/name.

```html
<!DOCTYPE html>
<html lang="en">
<head>
<meta charset="utf-8">
<title>Magnesium + B6 Label</title>
<link rel="stylesheet" href="https://fonts.googleapis.com/css2?family=Open+Sans:ital,wght@0,600;0,700;1,700&family=Nunito:wght@800&display=swap">
<style>
  :root {
    --mint-green: #237D62;
    --deep-green: #4a8a34;
    --mid-green: #7dbf3e;
    --fresh-green: #a6d95a;
    --pale-green: #dff1c4;
    --ink: #111111;
    --ginger: #f5a944;
    --ginger-edge: #b07a2c;
    --teal-pill: #86b8a7;
    --white: #ffffff;
    --page: #ffffff;
  }
  * { margin: 0; padding: 0; box-sizing: border-box; }
  html, body { width: 1200px; height: 1200px; overflow: hidden; background: var(--page); }
  .canvas { position: relative; width: 1200px; height: 1200px; }
  .label {
    position: absolute; left: 70px; top: 362px;
    width: 1060px; height: 475px; overflow: hidden;
    background:
      linear-gradient(180deg,
        var(--white) 0%,
        var(--white) 44%,
        var(--pale-green) 60%,
        var(--fresh-green) 76%,
        var(--mid-green) 88%,
        var(--deep-green) 100%);
  }
  .label-tint {
    position: absolute; inset: 0;
    background: linear-gradient(90deg, rgba(166,217,90,0) 0%, rgba(166,217,90,0) 55%, rgba(166,217,90,0.55) 100%);
  }
  .brand {
    position: absolute; left: 0; right: 0; top: 92px;
    text-align: center; color: var(--mint-green);
    font-family: "Open Sans", sans-serif; font-weight: 700;
  }
  .brand-name { font-size: 54px; letter-spacing: 1px; line-height: 1; }
  .brand-name sup { font-size: 14px; vertical-align: top; position: relative; top: 4px; margin-left: 2px; }
  .brand-sub { font-size: 17px; letter-spacing: 14px; margin-top: 8px; padding-left: 14px; line-height: 1; }
  .product-name {
    position: absolute; left: 298px; top: 226px;
    font-family: "Open Sans", sans-serif; font-weight: 600;
    font-size: 41px; color: var(--ink); letter-spacing: 0; line-height: 1;
  }
  .product-desc {
    position: absolute; left: 301px; top: 279px;
    width: 298px; height: 29px; border-radius: 8px;
    background: var(--ginger); box-shadow: 2px 2px 0 var(--ginger-edge);
    font-family: "Nunito", sans-serif; font-weight: 800; font-size: 19px;
    color: var(--ink); line-height: 29px; padding-left: 9px;
  }
  .category {
    position: absolute; left: 298px; top: 425px;
    font-family: "Open Sans", sans-serif; font-weight: 600;
    font-size: 20px; color: var(--white); letter-spacing: 0.5px;
  }
  .intake {
    position: absolute; left: 592px; top: 416px;
    width: 180px; height: 36px; border-radius: 18px;
    background: var(--white); display: flex; overflow: hidden;
  }
  .intake-count {
    width: 73px; background: var(--teal-pill); border-radius: 18px;
    text-align: center; font-family: "Open Sans", sans-serif; color: var(--ink);
  }
  .intake-count b { display: block; font-size: 22px; font-weight: 700; line-height: 24px; }
  .intake-count span { display: block; font-size: 6.5px; font-weight: 600; line-height: 8px; }
  .intake-dose {
    flex: 1; padding-left: 10px; font-family: "Open Sans", sans-serif;
    font-style: italic; font-weight: 700; color: var(--ink); line-height: 1;
  }
  .intake-dose .dose-label { display: block; font-size: 11px; margin: 5px 0 2px 6px; }
  .intake-dose .dose-value { display: block; font-size: 14px; }
</style>
</head>
<body>
<div class="canvas">
  <section class="label">
    <div class="label-tint" aria-hidden="true"></div>

    <div class="brand">
      <div class="brand-name">VERDANT<sup>®</sup></div>
      <div class="brand-sub">CALM</div>
    </div>

    <h1 class="product-name">MAGNESIUM + B6</h1>
    <p class="product-desc">Magnesium with ginger taste</p>

    <p class="category">DIETARY SUPPLEMENT</p>

    <div class="intake">
      <div class="intake-count"><b>60</b><span>CAPSULES</span></div>
      <div class="intake-dose">
        <span class="dose-label">Daily Intake</span>
        <span class="dose-value">1 CAPSULE</span>
      </div>
    </div>
  </section>
</div>
</body>
</html>
```